CREATE A BUSINESS CARD FOR A BOAT CLEANING SERVICE

WE ARE STARTING A NEW BOAT CLEANING BUSINESS. WE DIVE UNDERWATER TO CLEAN BOAT HULLS, JETTIES, UNDERWATER STRUCTURES ETC. WE ARE LOOKING FOR AN UPPERMARKET MODERN LOGO AND BUSINESS CARD AS ALOT OF OUR TARGET MARKET WILL BE HIGH END. YOU HAVE TO DESIGN A BUSINESS CARD AND LOGO SEPERATELY .
THE BUSINESS CARD DIMESNION MUST BE STANDARD SIZE.
The standard dimensions of a printed business card are 3.5 x 2 inches

Target Market(s)

UNDERWATER SERVICED

Industry/Entity Type

Business

Contact Information for Business Card

HOLLAND UNDERWATER SERVICES

Font styles to use
Serif

Colors

Designer to choose colors to be used in the design.

Requirements
Must have
• HOLLAND
Nice to have
• dark
Should not have
• more than 3 colors

```html
<!DOCTYPE html>
<html lang="en">
<head>
<meta charset="utf-8">
<title>Holland Underwater Services – Business Card</title>
<link rel="stylesheet" href="https://fonts.googleapis.com/css2?family=Montserrat:wght@300;400&family=Oswald:wght@400;600&family=Roboto+Condensed:wght@400&display=swap">
<style>
  :root {
    --backdrop: #26282c;
    --card-blue: #0e5a97;
    --card-blue-light: #1566a8;
    --emboss: #0a4778;
    --emboss-light: #2a78b6;
    --silver: #cdd7e1;
    --white: #ffffff;
  }
  * { box-sizing: border-box; margin: 0; padding: 0; }
  html, body {
    width: 1200px; height: 900px; overflow: hidden;
    background: var(--backdrop);
  }
  .canvas {
    width: 1200px; height: 900px;
    display: flex; align-items: center; justify-content: center; gap: 50px;
  }
  .card {
    width: 525px; height: 300px;
    border-radius: 26px;
    background: radial-gradient(circle at 40% 35%, var(--card-blue-light), var(--card-blue) 70%);
    position: relative;
    overflow: hidden;
  }
  .emboss {
    color: var(--emboss);
    text-shadow: 0 1px 0 var(--emboss-light);
  }

  /* Front */
  .card-front { display: flex; flex-direction: column; align-items: center; justify-content: center; }
  .brand-name {
    font-family: "Montserrat", sans-serif; font-weight: 300;
    color: var(--silver);
    font-size: 46px; letter-spacing: 14px; padding-left: 14px;
  }
  .brand-tagline {
    font-family: "Montserrat", sans-serif; font-weight: 300;
    color: var(--silver);
    font-size: 16px; letter-spacing: 5px; margin-top: 6px;
  }
  .partner-row { display: flex; align-items: center; gap: 28px; margin-top: 34px; }
  .partner-badge {
    width: 40px; height: 40px; border-radius: 50%;
    background: #0b3f66; border: 2px solid #3a86bf;
  }
  .partner-name {
    font-family: "Montserrat", sans-serif; font-weight: 400;
    color: var(--white); font-size: 20px; letter-spacing: 1px;
  }

  /* Back */
  .card-back { padding: 40px 40px 30px 44px; }
  .back-top { display: flex; align-items: flex-start; }
  .person { width: 190px; text-align: right; padding-right: 22px; padding-top: 4px; }
  .person-name {
    font-family: "Oswald", sans-serif; font-weight: 600;
    font-size: 30px; letter-spacing: 1px; line-height: 1.1;
  }
  .person-title {
    font-family: "Roboto Condensed", sans-serif; font-size: 14px; margin-top: 2px;
  }
  .divider { width: 1px; height: 92px; background: var(--emboss); box-shadow: 1px 0 0 var(--emboss-light); }
  .contacts { list-style: none; padding-left: 22px; padding-top: 4px; }
  .contacts li {
    display: flex; align-items: center; gap: 8px;
    font-family: "Roboto Condensed", sans-serif; font-size: 17px; line-height: 1.5;
  }
  .contacts svg { width: 11px; height: 11px; fill: var(--emboss); flex: none; }
  .address {
    position: absolute; left: 44px; bottom: 40px;
    font-family: "Roboto Condensed", sans-serif; font-size: 18px;
  }
</style>
</head>
<body>
<main class="canvas">
  <section class="card card-front" aria-label="Card front">
    <div class="brand-name">HOLLAND</div>
    <div class="brand-tagline">UNDERWATER SERVICE</div>
    <div class="partner-row">
      <div class="partner-badge" role="img" aria-label="Partner badge"></div>
      <div class="partner-name">HOLLAND</div>
    </div>
  </section>

  <section class="card card-back" aria-label="Card back">
    <div class="back-top">
      <div class="person emboss">
        <div class="person-name">MARK ELLIS</div>
        <div class="person-title">President</div>
      </div>
      <div class="divider"></div>
      <ul class="contacts emboss">
        <li>
          <svg viewBox="0 0 24 24" aria-hidden="true"><path d="M6.6 10.8a15 15 0 0 0 6.6 6.6l2.2-2.2a1 1 0 0 1 1-.25 11.4 11.4 0 0 0 3.6.57 1 1 0 0 1 1 1V20a1 1 0 0 1-1 1A17 17 0 0 1 3 4a1 1 0 0 1 1-1h3.5a1 1 0 0 1 1 1c0 1.25.2 2.45.57 3.57a1 1 0 0 1-.25 1z"/></svg>
          (410) 555-0148
        </li>
        <li>
          <svg viewBox="0 0 24 24" aria-hidden="true"><path d="M2 5h20v14H2zm2 2v.5l8 5 8-5V7zm0 2.8V17h16V9.8l-8 5z"/></svg>
          info@hollandunderwater.com
        </li>
        <li>
          <svg viewBox="0 0 24 24" aria-hidden="true"><circle cx="12" cy="12" r="10"/></svg>
          www.hollandunderwater.com
        </li>
      </ul>
    </div>
    <div class="address emboss">140, 318 - 9th Ave, SW Calgary, AB T2P 1K4</div>
  </section>
</main>
</body>
</html>
```